Church Website with Home Page and Member Sermon Library

I am in need of an updated design for our church website. This will include 4 pages (outlined below). We are a conservative, evangelical, Christian church. The site should be modern and clean, while still reflecting our conservative values. I already have a logo for our church, and I want the site to incorporate the logo, and match the logo/branding. Stock photos are allowed if needed, but I have uploaded some images of our church and would prefer those images to be used if possible. Any stock photos used should not include any people in the photos (scenery, nature, buildings, animals, etc. are fine).

The site will need 4 pages: Home, Support Us (Donate), Login, and Recording Library.

Page 1: Home
The home page should include the following sections:

- Navigation: Should include links to each section of the home page plus a "listen live" link which will take the user to a live-streaming site and a "support us" link which will take the user to a support/donate page.

- Announcements: Can be either a banner or some other design, but there needs to be some way for us to post announcements for visitors to see. I'm open for creative ideas in this section, but would like it not to take up a lot of room on the page.

- About Us: Should include address, service times (see attached document), and information about the church.

- Pastor Bio: A section that introduces our pastor and gives a short bio about our pastor. Would like this section to include a picture of our pastor. Somewhere in this section I would like to include this Bible reference: "And I will give you pastors according to mine heart, which shall feed you with knowledge and understanding. Jer 3:15 LPW"

- Articles of Faith (What We Believe): This should include several sub-sections each with a heading, body, and possibly 1 or more scripture references. I have attached a document to the brief that includes our articles of faith. Feel free to be creative with this section in how you lay these out and format them.

- Support Us: A small section that explains what kind of support someone can give and a link to a donation page. The link can say something like "Support Us" or "Donate Now".

- Contact form: A contact form that allows the visitor to send us a message. The contact form should ask for name, email, phone, and message.

- Footer: A footer that will be displayed on all pages of the site. This should include at a minimum a link to the home page (or a link to each individual section in the home page if you prefer), a link to "listen live", a link to "support us", a link to "contact us" (or you can put the contact form directly in the footer if you prefer), the address, and a "member login" link.

Page 2: Support Us
The donation page should include a form the visitor can fill out to make a donation. We will embed a third party form later. For this design, please just mock out the design with a basic form asking for name, phone, and email.

Page 3: Login
The recording library (detailed below) will require members to login with a shared numeric code before accessing the page. We need a design for a login screen. The screen should include navigation/footer just like all other pages, but the body of the login page will consist only of a form that asks the user to enter the access code and then a "login" button.

Page 4: Recording Library

The library page is a member-only page that will require a shared, numeric pass code to access. On this page, members will be able to access a filterable list of past sermons. The page by default should display most recent sermons, but should also include a search form that allows the member to filter the sermon list to find a particular sermon. The search form should allow the user to select a filter type (e.g. Speaker name, date, event, etc.) and type in a value to search. They should be able to add multiple filters and remove filters that have been added. Each sermon that is displayed in the result list should include basic information such as title, date, speaker, tags, etc. along with a download icon, and an embedded audio player where they can click a play button to stream it on-demand. Each sermon should also have clickable tags associated with it that can be used to find related sermons.
Updates

I have uploaded several images of our church. Feel free to incorporate these into your design if possible.

Target Market(s)

Church Members

Industry/Entity Type

Religion

Number of Pages Required

4 page

Font styles to use
Sans Serif

Colors

Designer to choose colors to be used in the design.

Requirements
Must have
• Must incorporate the logo (attached)
Nice to have
• Would like the design to incorporate pictures of our church (attached) instead of stock photos if possible.
Should not have
• Please avoid an overly cluttered design. Stock photos used should not include any people in the photos.

```html
<!DOCTYPE html>
<html lang="en">
<head>
<meta charset="utf-8">
<title>Grace Covenant Church</title>
<link href="https://fonts.googleapis.com/css2?family=Raleway:wght@400;500;600&display=swap" rel="stylesheet">
<style>
:root{
  --ink:#1f1f1f;
  --ink-2:#2b2b2b;
  --card:#3a3a3a;
  --gold:#c9a05a;
  --gold-soft:#b89a62;
  --orange:#e58a1f;
  --paper:#efefef;
  --white:#ffffff;
  --muted:#bdbdbd;
}
*{box-sizing:border-box;margin:0;padding:0}
html,body{width:1200px;height:3118px;overflow:hidden}
body{font-family:'Raleway',sans-serif;color:var(--white);background:var(--ink);position:relative}
.abs{position:absolute}
a{color:inherit;text-decoration:none}

/* hero */
.hero{position:absolute;left:0;top:0;width:1200px;height:625px;
  background:radial-gradient(circle at 50% 30%,#8a5a2a 0%,#5a3418 35%,#2e1a0c 70%,#1a0f07 100%)}
.nav a{position:absolute;top:50px;font-size:12px;font-weight:500}
.brand{position:absolute;left:0;width:1200px;top:72px;text-align:center;font-size:14px;letter-spacing:2px;font-weight:500}
.hero h1{position:absolute;left:0;width:1200px;top:200px;text-align:center;font-weight:400;font-size:61px;line-height:72px}
.btn{position:absolute;display:flex;align-items:center;justify-content:center;gap:14px;font-size:13px;font-weight:500;color:var(--white)}
.btn svg{width:8px;height:12px}
.hero .btn{left:533px;top:390px;width:134px;height:41px;background:rgba(20,12,6,.55);border:1px solid rgba(255,255,255,.6)}
.hero-foot{position:absolute;top:569px;font-size:12px;font-weight:500;white-space:nowrap}
.hero-social{position:absolute;top:569px;right:195px;display:flex;gap:30px;font-size:12px;font-weight:500;white-space:nowrap}

/* service */
.dark{position:absolute;left:0;top:625px;width:1200px;height:1340px;background:var(--ink)}
.photo{position:absolute}
.frame{position:absolute;border:2px solid var(--gold);border-radius:10px}
.slider-label{position:absolute;font-size:8px;letter-spacing:1px;color:var(--muted)}
h2{font-weight:400;font-size:38px;line-height:49px}
.copy{font-size:10px;line-height:17.5px;color:#d6d6d6}
.copy p+p{margin-top:8px}
.time{position:absolute;left:592px;width:223px;height:79px;background:#3d3d3d;border-radius:3px;padding:12px 12px}
.time .day{display:flex;align-items:center;gap:7px;color:var(--gold-soft);font-size:14px}
.time .hours{margin-top:8px;font-size:18px;font-weight:500}
.gold-btn{border:1px solid var(--gold);background:transparent}
.caption{position:absolute;left:735px;top:1791px;width:168px;height:29px;background:var(--gold);color:var(--ink);font-size:14px;display:flex;align-items:center;padding-left:8px;gap:6px;white-space:nowrap}
.caption i{width:7px;height:7px;border-radius:50%;background:var(--ink);display:block}

/* sermons */
.light{position:absolute;left:0;top:1965px;width:1200px;height:877px;background:linear-gradient(135deg,#f4f4f4,#e6e6e6 50%,#f2f2f2)}
.light h2{position:absolute;left:0;width:1200px;top:100px;text-align:center;color:var(--ink)}
.sermon{position:absolute;width:191px;height:227px;background:var(--ink-2);text-align:center}
.sermon .avatar{position:absolute;left:81px;top:25px;width:29px;height:29px;border-radius:50%;background:linear-gradient(135deg,#8a8f96,#c9b59a)}
.sermon .by{position:absolute;left:0;width:100%;top:62px;font-size:9px}
.sermon .title{position:absolute;left:24px;width:143px;top:88px;font-size:14.5px;line-height:19px;font-weight:500}
.sermon .tag{position:absolute;left:67px;top:157px;width:57px;height:15px;background:var(--white);color:var(--orange);font-size:7.5px;line-height:15px}
.player{position:absolute;left:13px;top:194px;width:166px;height:22px}
.player .play{position:absolute;left:0;top:0;width:22px;height:22px;border-radius:50%;background:var(--white)}
.player .track{position:absolute;left:30px;top:10px;width:114px;height:2px;background:#d0d0d0}
.player .fill{position:absolute;left:0;top:0;width:30px;height:2px;background:var(--orange)}
.player .clock{position:absolute;right:0;top:6px;font-size:7px}

/* announcements */
.announce{position:absolute;left:0;top:2842px;width:1200px;height:276px;background:var(--ink)}
.announce h2{position:absolute;left:0;width:1200px;top:92px;text-align:center}
.notice{position:absolute;top:182px;height:94px;overflow:hidden}
.notice-a{left:196px;width:407px;background:var(--gold)}
.notice-b{left:619px;width:386px;background:#f5f5f5;color:var(--ink)}
</style>
</head>
<body>

<header class="hero" role="img" aria-label="Photo looking up into the ornate domed ceiling of the church">
  <nav class="nav">
    <a href="#" style="left:195px">Home</a>
    <a href="#" style="left:264px">About</a>
    <a href="#" style="left:334px">Pastor</a>
    <a href="#" style="left:800px">Library</a>
    <a href="#" style="left:877px">Donation</a>
    <a href="#" style="left:962px">Contact</a>
  </nav>
  <div class="brand">GRACE COVENANT</div>
  <h1>I am the way, and the<br>truth and the life.</h1>
  <a href="#" class="btn">Book A visit <svg viewBox="0 0 8 12"><path d="M1 1l5 5-5 5" fill="none" stroke="#fff" stroke-width="1.5"/></svg></a>
  <a href="#" class="hero-foot" style="left:195px">Stream Sermons</a>
  <div class="hero-social">
    <a href="#">Fellowship Feed</a>
    <a href="#">Photo Journal</a>
  </div>
</header>

<section class="dark">
  <div class="photo" style="left:131px;top:102px;width:408px;height:482px;background:radial-gradient(circle at 50% 35%,#d98a3a,#7a3e14 50%,#2a160a 100%)" role="img" aria-label="Photo of a wooden cross beside an open Bible in warm candlelight"></div>
  <div class="frame" style="left:147px;top:117px;width:376px;height:452px"></div>
  <span class="slider-label" style="left:219px;top:598px">PREV</span>
  <span class="abs" style="left:254px;top:602px;width:249px;height:1px;background:#666"></span>
  <span class="abs" style="left:254px;top:601px;width:144px;height:2px;background:#ddd"></span>
  <span class="slider-label" style="left:513px;top:598px">NEXT</span>

  <h2 class="abs" style="left:593px;top:117px">Grace Covenant<br>Church Service Time</h2>
  <div class="copy abs" style="left:592px;top:225px;width:405px">
    <p>Printer took a galley of type and scrambled it to make a type specimen book. It has survived not only five centuries, but also the leap into electronic typesetting, remaining essentially unchanged.</p>
    <p>It was popularised in the 1960s with the release of Letraset sheets containing Lorem Ipsum passages, and more recently with desktop publishing</p>
  </div>
  <div class="time" style="top:349px">
    <div class="day"><svg width="15" height="14" viewBox="0 0 15 14"><rect x="1" y="2" width="12" height="11" rx="1" fill="none" stroke="#b89a62"/><path d="M1 5h12M4 0v3M10 0v3" stroke="#b89a62"/></svg>Monday Friday</div>
    <div class="hours">9:00am - 5:30pm PST</div>
  </div>
  <div class="time" style="top:444px">
    <div class="day"><svg width="15" height="14" viewBox="0 0 15 14"><rect x="1" y="2" width="12" height="11" rx="1" fill="none" stroke="#b89a62"/><path d="M1 5h12M4 0v3M10 0v3" stroke="#b89a62"/></svg>Saturday &amp; Sunday</div>
    <div class="hours">9:00am - 8:30pm PST</div>
  </div>
  <a href="#" class="btn gold-btn" style="left:592px;top:557px;width:135px;height:41px">Book A visit <svg viewBox="0 0 8 12"><path d="M1 1l5 5-5 5" fill="none" stroke="#fff" stroke-width="1.5"/></svg></a>

  <h2 class="abs" style="left:195px;top:803px">Pastor of Grace<br>Covenant Church</h2>
  <div class="copy abs" style="left:195px;top:919px;width:418px">
    <p>Printer took a galley of type and scrambled it to make a type specimen book. It has survived not only five centuries, but also the leap into electronic typesetting, remaining essentially unchanged.</p>
    <p>desktop publishing packages and web page editors now use Lorem Ipsum as their default model text, and a search for 'lorem ipsum' will uncover many web sites still in their infancy. Various versions have evolved over the years, sometimes by accident, sometimes on purpose desktop publishing packages and web page editors now use Lorem Ipsum as their default model text, and a search for 'lorem ipsum' will uncover many web sites still in their infancy. Various versions have evolved over the years, sometimes by accident, sometimes on purpose</p>
  </div>
  <a href="#" class="btn" style="left:195px;top:1138px;width:134px;height:41px;border:1px solid #fff">Know More <svg viewBox="0 0 8 12"><path d="M1 1l5 5-5 5" fill="none" stroke="#fff" stroke-width="1.5"/></svg></a>
</section>

<div class="abs" style="left:694px;top:1419px;width:310px;height:401px;border:12px solid var(--gold)"></div>
<div class="photo" style="left:727px;top:1330px;width:230px;height:490px;background:linear-gradient(180deg,rgba(40,40,40,0) 0%,#2a2a2a 25%,#151515 60%,#1b1b1b 100%)" role="img" aria-label="Portrait of the pastor in robes holding a Bible"></div>
<div class="caption"><i></i>Pastor Daniel Reed</div>

<section class="light">
  <h2>Sermon Recordings<br>/ Live-streaming</h2>
</section>

<div class="sermon" style="left:195px;top:2193px"><div class="avatar" role="img" aria-label="Speaker avatar"></div><div class="by">Spoken By Ruth K.</div><div class="title">Printer took a galley of type and scrambled it to</div><div class="tag">Sermon 1</div><div class="player"><span class="play"><svg width="22" height="22"><path d="M9 7l6 4-6 4z" fill="#e58a1f"/></svg></span><span class="track"><span class="fill"></span></span><span class="clock">00:10</span></div></div>
<div class="sermon" style="left:401px;top:2193px"><div class="avatar" role="img" aria-label="Speaker avatar"></div><div class="by">Spoken By Ruth K.</div><div class="title">Printer took a galley of type and scrambled it to</div><div class="tag">Sermon 2</div><div class="player"><span class="play"><svg width="22" height="22"><path d="M9 7l6 4-6 4z" fill="#e58a1f"/></svg></span><span class="track"><span class="fill"></span></span><span class="clock">00:10</span></div></div>
<div class="sermon" style="left:607px;top:2193px"><div class="avatar" role="img" aria-label="Speaker avatar"></div><div class="by">Spoken By Ruth K.</div><div class="title">Printer took a galley of type and scrambled it to</div><div class="tag">Sermon 3</div><div class="player"><span class="play"><svg width="22" height="22"><path d="M9 7l6 4-6 4z" fill="#e58a1f"/></svg></span><span class="track"><span class="fill"></span></span><span class="clock">00:10</span></div></div>
<div class="sermon" style="left:814px;top:2193px"><div class="avatar" role="img" aria-label="Speaker avatar"></div><div class="by">Spoken By Ruth K.</div><div class="title">Printer took a galley of type and scrambled it to</div><div class="tag">Sermon 4</div><div class="player"><span class="play"><svg width="22" height="22"><path d="M9 7l6 4-6 4z" fill="#e58a1f"/></svg></span><span class="track"><span class="fill"></span></span><span class="clock">00:10</span></div></div>
<div class="sermon" style="left:195px;top:2434px"><div class="avatar" role="img" aria-label="Speaker avatar"></div><div class="by">Spoken By Ruth K.</div><div class="title">Printer took a galley of type and scrambled it to</div><div class="tag">Sermon 1</div><div class="player"><span class="play"><svg width="22" height="22"><path d="M9 7l6 4-6 4z" fill="#e58a1f"/></svg></span><span class="track"><span class="fill"></span></span><span class="clock">00:10</span></div></div>
<div class="sermon" style="left:401px;top:2434px"><div class="avatar" role="img" aria-label="Speaker avatar"></div><div class="by">Spoken By Ruth K.</div><div class="title">Printer took a galley of type and scrambled it to</div><div class="tag">Sermon 2</div><div class="player"><span class="play"><svg width="22" height="22"><path d="M9 7l6 4-6 4z" fill="#e58a1f"/></svg></span><span class="track"><span class="fill"></span></span><span class="clock">00:10</span></div></div>
<div class="sermon" style="left:607px;top:2434px"><div class="avatar" role="img" aria-label="Speaker avatar"></div><div class="by">Spoken By Ruth K.</div><div class="title">Printer took a galley of type and scrambled it to</div><div class="tag">Sermon 3</div><div class="player"><span class="play"><svg width="22" height="22"><path d="M9 7l6 4-6 4z" fill="#e58a1f"/></svg></span><span class="track"><span class="fill"></span></span><span class="clock">00:10</span></div></div>
<div class="sermon" style="left:814px;top:2434px"><div class="avatar" role="img" aria-label="Speaker avatar"></div><div class="by">Spoken By Ruth K.</div><div class="title">Printer took a galley of type and scrambled it to</div><div class="tag">Sermon 4</div><div class="player"><span class="play"><svg width="22" height="22"><path d="M9 7l6 4-6 4z" fill="#e58a1f"/></svg></span><span class="track"><span class="fill"></span></span><span class="clock">00:10</span></div></div>

<a href="#" class="btn abs" style="left:528px;top:2710px;width:143px;height:40px;background:var(--ink)">Explorer More <svg viewBox="0 0 8 12"><path d="M1 1l5 5-5 5" fill="none" stroke="#fff" stroke-width="1.5"/></svg></a>

<section class="announce">
  <h2>Important Announcement</h2>
  <div class="notice notice-a">
    <div class="abs" style="left:50px;top:20px;width:110px;height:74px;background:radial-gradient(circle at 40% 40%,#fff 0%,#f0d9a8 40%,#c9a05a 75%)" role="img" aria-label="Illustration of a megaphone"></div>
    <div class="abs" style="left:268px;top:14px;color:var(--ink);font-size:29px;font-weight:600;line-height:36px;text-align:right;width:120px">Chruch<br><span style="color:#fff">Closed</span></div>
  </div>
  <div class="notice notice-b">
    <div class="abs" style="left:16px;top:22px;font-size:10px;font-weight:500;letter-spacing:1px">GRACE COVENANT</div>
    <div class="abs" style="left:214px;top:14px;font-size:15px;white-space:nowrap">*Service time Change</div>
    <div class="abs" style="left:95px;top:50px;width:220px;height:44px;background:linear-gradient(100deg,#f5f5f5 0%,#f4a03a 30%,#ef6a1a 60%,#f7d34a 100%)" role="img" aria-label="Abstract colourful illustration"></div>
  </div>
</section>

</body>
</html>
```